Small Business Consulting Firm Needs Letterhead

We need a letterhead for our company "Brightpath Plus". Our company does outbound calling and mailing to business owner's companies who have taken high interest loans. These loans tend to put these businesses in a big financial bind short term, and we help them find better financial options. We would like the design to match our colors of our logo. Headers and footers would look nice, but we are open. We would want it to include our address, website, phone, and email info. Our address - 2000 E. Lamar Blvd. Suite 600Website - www.safeguardtoday.comEmail - info@safeguardtoday.comPhone - 855-726-1938
Industry/Entity Type
Financial Planning
Look and feel
Each slider illustrates characteristics of the customer's brand and the style your logo design should communicate.

```html
<!DOCTYPE html>
<html lang="en">
<head>
<meta charset="utf-8">
<title>Brightpath Plus Letterhead</title>
<link rel="stylesheet" href="https://fonts.googleapis.com/css2?family=Montserrat:wght@400;500&display=swap">
<style>
  :root {
    --bg: #e9e9e9;
    --paper: #ffffff;
    --green: #6aa53b;
    --green-soft: #8cc45a;
    --blue: #1a7fc1;
    --ink: #2b2b2b;
    --rule: #555555;
  }
  * { margin: 0; padding: 0; box-sizing: border-box; }
  html, body { width: 1200px; height: 1200px; overflow: hidden; background: var(--bg); }
  body { font-family: "Montserrat", sans-serif; color: var(--ink); }

  .letterhead {
    position: absolute; left: 167px; top: 40px;
    width: 866px; height: 1120px;
    background: var(--paper);
    box-shadow: 0 4px 14px rgba(0,0,0,.18);
  }
  .side-band { position: absolute; left: 0; top: 0; width: 52px; height: 1120px; background: var(--green); }
  .side-band::after {
    content: ""; position: absolute; right: 0; top: 0; width: 6px; height: 100%;
    background: var(--green-soft);
  }
  .footer-accent { position: absolute; left: 52px; top: 1030px; width: 36px; height: 8px; background: var(--blue); }

  .brand { position: absolute; top: 146px; left: 52px; right: 0; text-align: center; }
  .brand-name { font-size: 26px; font-weight: 400; letter-spacing: 1.5px; text-transform: uppercase; color: #3a3a3a; }

  .letter { position: absolute; left: 108px; width: 706px; font-size: 15px; letter-spacing: 0.85px; line-height: 22.5px; }
  .date { top: 270px; }
  .recipient { top: 329px; font-style: normal; }
  .salutation { top: 472px; }
  .body-copy { top: 506px; text-align: justify; line-height: 25.4px; }
  .body-copy p + p { margin-top: 4px; }
  .closing { top: 822px; }
  .signer { top: 877px; }
  .signer-name { font-size: 17px; font-weight: 500; letter-spacing: 0.6px; }
  .signer-role { letter-spacing: 4px; }

  .contact { position: absolute; left: 343px; width: 475px; top: 1025px; font-size: 13.5px; letter-spacing: 1px; }
  .contact-row { display: flex; justify-content: space-between; align-items: center; height: 22px; }
  .contact-row.first { border-bottom: 1.2px solid var(--rule); padding-bottom: 4px; margin-bottom: 4px; }
  .contact-item { display: flex; align-items: center; gap: 8px; }
  .contact-item svg { width: 11px; height: 11px; flex: none; }
  .contact-item.phone { letter-spacing: 3px; }
</style>
</head>
<body>
  <main class="letterhead">
    <div class="side-band" aria-hidden="true"></div>
    <div class="footer-accent" aria-hidden="true"></div>

    <header class="brand">
      <div class="brand-name">Brightpath Plus</div>
    </header>

    <p class="letter date">Date: 20 November 2018</p>

    <address class="letter recipient">
      To<br>Oakfield Supply Ltd.<br>58 Harrow Lane, Suite# B<br>London, UK 4300B17
    </address>

    <p class="letter salutation">Dear Carter,</p>

    <div class="letter body-copy">
      <p>Lorem Ipsum is simply dummy text of the printing and typesetting industry. Lorem Ipsum has been the industry's standard dummy text ever since the 1500s, when an unknown printer took a galley of type and scrambled it to make a type specimen book. It has survived not only five centuries, but also the leap into electronic type-setting, remaining essentially unchanged. It was popularised in the 1960s with the release of Typeline sheets containing Lorem Ipsum passages, and more recently with desktop publishing software like Pagecraft Studio including versions of Lorem Ipsum.</p>
      <p>Lorem Ipsum is simply dummy text of the printing and typesetting industry. Lorem Ipsum has been the industry's.</p>
    </div>

    <p class="letter closing">Thanking you</p>

    <div class="letter signer">
      <div class="signer-name">Martin Reyes Cole</div>
      <div class="signer-role">CEO</div>
    </div>

    <footer class="contact">
      <div class="contact-row first">
        <span class="contact-item phone">
          <svg viewBox="0 0 12 12" aria-hidden="true"><path d="M2.5 1 L4.5 1 L5.3 3.6 L4 4.6 Q5 7 7.4 8 L8.4 6.7 L11 7.5 L11 9.5 Q10.5 11 9 11 Q1 10 1 3 Q1 1.5 2.5 1Z" fill="var(--blue)"/></svg>
          855-726-1938
        </span>
        <span class="contact-item">
          <svg viewBox="0 0 12 12" aria-hidden="true"><rect x="0.5" y="2.5" width="11" height="7.5" rx="1" fill="var(--blue)"/><path d="M1 3 L6 6.8 L11 3" stroke="#fff" stroke-width="1" fill="none"/></svg>
          info@brightpathplus.com
        </span>
      </div>
      <div class="contact-row">
        <span class="contact-item">
          <svg viewBox="0 0 12 12" aria-hidden="true"><circle cx="6" cy="6" r="5" fill="none" stroke="var(--green)" stroke-width="1.3"/><path d="M1 6 H11 M6 1 Q3 6 6 11 M6 1 Q9 6 6 11" stroke="var(--green)" stroke-width="1" fill="none"/></svg>
          www.brightpathplus.com
        </span>
        <span class="contact-item">
          <svg viewBox="0 0 12 12" aria-hidden="true"><path d="M6 11.5 Q1.5 6 1.5 4.5 A4.5 4.5 0 0 1 10.5 4.5 Q10.5 6 6 11.5Z" fill="var(--green)"/><circle cx="6" cy="4.5" r="1.6" fill="#fff"/></svg>
          4170 W. Corwin Ave. Suite 310
        </span>
      </div>
    </footer>
  </main>
</body>
</html>
```